Business Card Design

New business card design

Target Market(s)

Residential & Commercial Property Managers

Industry/Entity Type

Plumbing Services

Contact Information for Business Card

Name - Rowan Keddle, title - Director, Phone Number - 0431 286 517, email - rowan@tbk-plumbing.com.au, Company ABN - 73 215 904 386,

Font styles to use
Sans Serif

Colors
0054AA
0677BA
7BADD7
CADEEF
E8F1F8

```html
<!DOCTYPE html>
<html lang="en">
<head>
<meta charset="utf-8">
<title>TBK Plumbing Services – Business Card</title>
<link href="https://fonts.googleapis.com/css2?family=Montserrat:wght@400;600&display=swap" rel="stylesheet">
<style>
  :root {
    --ink: #1e2329;
    --paper: #ffffff;
    --brand-blue: #0677BA;
    --sky: #2fa6e0;
    --page: #e8ecef;
    --tag-dark: #5a5048;
    --tag-light: #d9dde1;
  }
  * { margin: 0; padding: 0; box-sizing: border-box; }
  html, body {
    width: 1200px; height: 880px; overflow: hidden;
    background: var(--page);
    font-family: "Montserrat", sans-serif;
  }
  .sheet {
    width: 1200px; height: 880px;
    display: flex; flex-direction: column; align-items: center; justify-content: center; gap: 40px;
  }
  .card {
    position: relative;
    width: 680px; height: 388px;
    border-radius: 26px;
    overflow: hidden;
    box-shadow: 0 10px 28px rgba(0,0,0,.18);
  }
  .card--front { background: var(--ink); }
  .card--back { background: var(--paper); }
  .card__art { position: absolute; inset: 0; }

  .wordmark {
    position: absolute;
    display: flex; align-items: center; gap: 18px;
    font-weight: 400;
    white-space: nowrap;
  }
  .wordmark__dot { width: 26px; height: 26px; border-radius: 50%; background: var(--sky); flex: none; }
  .wordmark__text { display: flex; flex-direction: column; line-height: 1; }
  .wordmark__name { font-size: 92px; letter-spacing: 6px; text-transform: lowercase; }
  .wordmark__tag { font-size: 16px; letter-spacing: 9px; text-transform: lowercase; margin-top: 10px; white-space: nowrap; }

  .card--front .wordmark { left: 50%; top: 50%; transform: translate(-50%, -50%); color: var(--paper); }
  .card--front .wordmark__tag { color: var(--tag-light); }
  .card--back .wordmark { left: 112px; top: 36px; color: var(--ink); }
  .card--back .wordmark__tag { color: var(--tag-dark); }

  .person {
    position: absolute; right: 370px; top: 290px; text-align: right; white-space: nowrap;
  }
  .person__name { color: var(--sky); font-weight: 600; font-size: 25px; line-height: 1.1; }
  .person__role { color: var(--paper); font-size: 16px; margin-top: 4px; }

  .divider {
    position: absolute; left: 326px; top: 278px; width: 1.5px; height: 64px; background: var(--sky);
  }
  .contacts {
    position: absolute; left: 342px; top: 280px; list-style: none;
    color: var(--paper); font-size: 15px; white-space: nowrap;
  }
  .contacts li { display: flex; align-items: center; gap: 9px; height: 26px; }
  .contacts svg { width: 15px; height: 15px; flex: none; }

  .abn {
    position: absolute; left: 0; right: 0; top: 352px; text-align: center;
    color: var(--paper); font-size: 15px; padding-left: 60px; white-space: nowrap;
  }
</style>
</head>
<body>
<main class="sheet">

  <section class="card card--front" aria-label="Business card front">
    <div class="wordmark">
      <span class="wordmark__dot"></span>
      <span class="wordmark__text">
        <span class="wordmark__name">TBK</span>
        <span class="wordmark__tag">plumbing services</span>
      </span>
    </div>
  </section>

  <section class="card card--back" aria-label="Business card back">
    <svg class="card__art" viewBox="0 0 680 388" preserveAspectRatio="none" aria-hidden="true">
      <defs>
        <linearGradient id="swoosh-fade" x1="0" y1="0" x2="680" y2="0" gradientUnits="userSpaceOnUse">
          <stop offset="0.12" stop-color="#2fa6e0" stop-opacity="0"/>
          <stop offset="0.40" stop-color="#2fa6e0" stop-opacity="1"/>
          <stop offset="1" stop-color="#2fa6e0" stop-opacity="1"/>
        </linearGradient>
      </defs>
      <path d="M0,268 C250,262 520,210 680,40 L680,388 L0,388 Z" fill="var(--ink)"/>
      <path d="M0,261 C250,255 520,202 680,32 L680,40 C520,210 250,262 0,268 Z" fill="var(--paper)"/>
      <path d="M0,262 C250,256 520,204 680,34" fill="none" stroke="url(#swoosh-fade)" stroke-width="3.5"/>
    </svg>

    <div class="wordmark">
      <span class="wordmark__dot"></span>
      <span class="wordmark__text">
        <span class="wordmark__name">TBK</span>
        <span class="wordmark__tag">plumbing services</span>
      </span>
    </div>

    <div class="person">
      <p class="person__name">Rowan Keddle</p>
      <p class="person__role">Director</p>
    </div>

    <span class="divider"></span>

    <ul class="contacts">
      <li>
        <svg viewBox="0 0 24 24" aria-hidden="true"><path fill="var(--sky)" d="M6.6 10.8a15.1 15.1 0 0 0 6.6 6.6l2.2-2.2c.3-.3.7-.4 1-.2 1.1.4 2.3.6 3.6.6.6 0 1 .4 1 1V20c0 .6-.4 1-1 1A17 17 0 0 1 3 4c0-.6.4-1 1-1h3.5c.6 0 1 .4 1 1 0 1.3.2 2.5.6 3.6.1.3 0 .7-.2 1z"/></svg>
        <span>0431 286 517</span>
      </li>
      <li>
        <svg viewBox="0 0 24 24" aria-hidden="true"><rect x="2" y="5" width="20" height="14" rx="2" fill="var(--sky)"/><path d="M3 6.5l9 6.5 9-6.5" fill="none" stroke="var(--ink)" stroke-width="1.6"/></svg>
        <span>rowan@tbk-plumbing.com.au</span>
      </li>
    </ul>

    <p class="abn">Company ABN - 73 215 904 386</p>
  </section>

</main>
</body>
</html>
```